New business card/stationary for a consulting company

I am looking for a clean and very professional looking business card for my consulting company as well as corresponding stationary. I am uploading our logo. I like simple and powerful for the feel. No graphics but I am open on everything else. Below is my contact information but would like the final to be in a version I can add my employees information into and print. Thank you.

Daniel Whitcombe
dan@ferncliffadvisory.com
2870 North 9th Avenue, Summit Floor, Elm Ridge, Illinois 60531
www.ferncliffadvisory.com

Industry/Entity Type

Consulting

Contact Information for Business Card

Daniel Whitcombe
dan@ferncliffadvisory.com
www.ferncliffadvisory.com

Font styles to use
Serif
Sans Serif

Requirements
Must have
• Our logo and the business card details.
Nice to have
• our website www.ferncliffadvisory.com

```html
<!DOCTYPE html>
<html lang="en">
<head>
<meta charset="utf-8">
<title>Ferncliff Advisory – Business Card</title>
<link rel="stylesheet" href="https://fonts.googleapis.com/css2?family=Questrial&family=Open+Sans:wght@400&display=swap">
<style>
  :root {
    --navy: #05075f;
    --paper: #ffffff;
    --backdrop: #e9e6e3;
    --silver: #d9dadf;
  }
  * { box-sizing: border-box; margin: 0; padding: 0; }
  html, body { width: 1200px; height: 900px; overflow: hidden; }
  body { background: var(--backdrop); position: relative; font-family: "Open Sans", sans-serif; }

  .card { position: absolute; box-shadow: 0 4px 14px rgba(0,0,0,.18); overflow: hidden; }

  /* Front */
  .card-front { left: 178px; top: 75px; width: 588px; height: 362px; background: var(--paper); }
  .brand-square { position: absolute; left: 274px; top: 58px; width: 40px; height: 40px; background: var(--navy); }
  .brand-name {
    position: absolute; left: 0; right: 0; top: 124px; text-align: center;
    font-family: "Questrial", sans-serif; font-size: 26px; letter-spacing: 1px;
    color: var(--navy); text-transform: uppercase;
  }
  .rule-thin { position: absolute; left: 0; top: 194px; width: 100%; height: 8px; background: var(--navy); }
  .contact-band { position: absolute; left: 0; top: 207px; width: 100%; height: 155px; background: var(--navy); color: #fff; }
  .person-name {
    position: absolute; left: 0; right: 0; top: 28px; text-align: center;
    font-family: "Questrial", sans-serif; font-size: 19px; letter-spacing: 1px; text-transform: uppercase;
  }
  .contact-links { position: absolute; right: 311px; top: 71px; text-align: right; font-size: 14.5px; line-height: 22px; }
  .contact-links span { display: inline-flex; align-items: center; gap: 5px; }
  .contact-links svg { width: 13px; height: 13px; }
  .divider { position: absolute; left: 293px; top: 70px; width: 1px; height: 52px; background: #fff; }
  .address { position: absolute; left: 315px; top: 64px; font-size: 14.5px; line-height: 22px; font-style: normal; }

  /* Back */
  .card-back { left: 388px; top: 505px; width: 566px; height: 352px; background: var(--navy); }
  .back-mark { position: absolute; left: 0; right: 0; top: 160px; display: flex; justify-content: center; align-items: center; gap: 14px; }
  .back-mark .mark-square { width: 26px; height: 26px; background: var(--silver); }
  .back-mark .brand-name-back {
    font-family: "Questrial", sans-serif; font-size: 28px; letter-spacing: 1px;
    color: var(--silver); text-transform: uppercase;
  }
</style>
</head>
<body>
  <section class="card card-front">
    <div class="brand-square"></div>
    <div class="brand-name">Ferncliff Advisory</div>
    <div class="rule-thin"></div>
    <div class="contact-band">
      <div class="person-name">Daniel Whitcombe</div>
      <div class="contact-links">
        <span>dan@ferncliffadvisory.com
          <svg viewBox="0 0 14 14" aria-hidden="true"><rect x="1" y="3" width="12" height="8" fill="#fff"/><path d="M1 3 L7 8 L13 3" fill="none" stroke="#05075f" stroke-width="1.2"/></svg>
        </span><br>
        <span>www.ferncliffadvisory.com
          <svg viewBox="0 0 14 14" aria-hidden="true"><circle cx="7" cy="7" r="6" fill="#fff"/><path d="M4 5 Q6 4 7 6 T10 9 M5 9 Q6 10 7 11" fill="none" stroke="#05075f" stroke-width="1.2"/></svg>
        </span>
      </div>
      <div class="divider"></div>
      <address class="address">2870 North 9th Avenue,<br>Summit Floor, Elm Ridge,<br>Illinois 60531</address>
    </div>
  </section>

  <section class="card card-back">
    <div class="back-mark">
      <div class="mark-square"></div>
      <div class="brand-name-back">Ferncliff Advisory</div>
    </div>
  </section>
</body>
</html>
```